Law Firm Web Design Project

I need a website design for my law firm. I have attached to this description the URL of a website I liked with a description of the elements of that website that appeal to me.

I am also attaching my law firm's logo, so you can review that design when you create the website design.

Reference Site: www.harborfieldcounsel-example.com

What we like about this site:
• The different layers
• Subtle designs, textures, curves
• 3 dimensional
• Floating effect
• Simple logo that stands out (we are providing logo)
• Prominent phone number
• Location of Areas of Practice
oDivorce, Legal Separation, Paternity, Spousal Maintenance, Child Custody, Child Support, Protective Orders, Community Property, Business Evaluations
• The limited amount of links across the top
o Home, Meet Our Attorney, FAQ, Contact Us
• Request A Consultation click through
• Right side bar with the moving icons
• Badges

Other Tips:
• We don’t want the website to be dark. The logo can standout and the website can have its own colors and flow.
• We would like there to be a “call to action” or way to get in touch on every page and every page view
• We would like a place for credit card icons at the bottom of the page
• Strong, yet elegant
• Finally, just use the website provided as a guide. Explore different colors, textures, shapes, shadows etc.
Updates

I would prefer the website have colors that are complementary to my logo and that are strong and elegant.  I like black, gold, amber, and tan colors.  Black should be used sparingly as an accent only, since I don't want the website to be too dark.

Please review the website I provided as an example in my project description.  I really like the three dimensional aspects of that website (web page floating on top of a background and the logo in the upper left floating on top of the web page).  I also like the use of "swirling" on the background and the webpage.  I hope this additional information is helpful.

Requirements
Must have
• I need a place to insert "client testimonials", a place to insert four logos of awards the law firm has received, a place for people to fill out a form to contact the law firm via email, and a place for people to click to review articles I have written.

```html
<!DOCTYPE html>
<html lang="en">
<head>
<meta charset="utf-8">
<title>Ashcombe Law</title>
<link href="https://fonts.googleapis.com/css2?family=Cabin:ital,wght@0,400;0,500;1,400&family=Open+Sans:wght@400;600&display=swap" rel="stylesheet">
<style>
:root{
  --backdrop:#e9dac7;
  --page:#fcf5ec;
  --tab:#f5e2cf;
  --tan-light:#efd3b4;
  --tan-dark:#d9a77a;
  --brown:#5b3519;
  --amber:#c7894a;
  --gold:#c79a5b;
  --orange:#ee8a2a;
  --orange-dark:#cf6d18;
  --grey-text:#6d6058;
  --hero-grey:#9b9690;
  --white:#ffffff;
}
*{box-sizing:border-box;margin:0;padding:0}
html,body{width:969px;height:1200px;overflow:hidden}
body{background:var(--backdrop);font-family:"Open Sans",sans-serif;position:relative}
.abs{position:absolute}
.page{left:45px;top:0;width:878px;height:1180px;background:var(--page);box-shadow:0 0 12px rgba(150,110,70,.25)}
.header-swirl{left:45px;top:0}
.brand{left:88px;top:40px;display:flex;align-items:center;gap:12px}
.brand-mark{width:22px;height:22px;border-radius:50%;background:var(--brown)}
.brand-name{font-family:"Cabin",sans-serif;font-weight:500;font-size:30px;color:var(--gold);letter-spacing:1px;white-space:nowrap}
.phone-bar{left:462px;top:9px;width:188px;height:40px;background:var(--tan-light);border-radius:0 8px 8px 0;display:flex;align-items:center;gap:10px;padding-left:6px}
.phone-bar span{font-family:"Cabin",sans-serif;font-size:14px;color:var(--white);white-space:nowrap}
.hero-photo{left:535px;top:20px;width:380px;height:360px;background:radial-gradient(ellipse at 55% 55%,#e8c9a6 0%,#f3e3d0 55%,rgba(252,245,236,0) 80%)}
.hero-box{left:85px;top:185px;width:410px;height:115px;background:rgba(255,255,255,.85);box-shadow:0 0 14px 6px rgba(240,230,220,.9);border-radius:6px;text-align:center;font-family:"Cabin",sans-serif;font-size:24px;letter-spacing:1px}
.hero-box .line1{color:var(--hero-grey);margin-top:24px}
.hero-box .line2{color:var(--gold);margin-top:8px}
.nav-tab{top:348px;height:37px;background:var(--tab);border-radius:8px 8px 0 0;font-family:"Cabin",sans-serif;font-size:13px;color:var(--amber);text-align:center;line-height:37px;font-weight:500;white-space:nowrap}
.content-band{left:45px;top:385px;width:878px;height:215px;background:var(--white)}
.about{left:53px;top:398px;width:862px;height:200px;background:linear-gradient(180deg,#f9ebdc,#fdf7f0);border-radius:22px 0 0 0}
.about h1{position:absolute;left:34px;top:10px;font-family:"Cabin",sans-serif;font-weight:400;font-size:24px;color:var(--brown)}
.about h2{position:absolute;left:33px;top:43px;font-family:"Cabin",sans-serif;font-weight:400;font-size:14px;color:var(--amber)}
.about p{position:absolute;left:31px;top:70px;width:562px;font-size:10.1px;line-height:16.5px;color:var(--grey-text);text-align:justify}
.side-card{border-radius:8px;background:linear-gradient(180deg,var(--tan-light),var(--tan-dark));box-shadow:0 3px 10px rgba(150,100,60,.35);border:2px solid #f6e4d2}
.side-card h3{font-family:"Cabin",sans-serif;font-weight:400;font-size:17px;color:var(--brown);margin:18px 0 12px 20px}
.side-item{margin:0 16px 0 20px;padding:6px 0 10px;border-bottom:1px solid rgba(255,255,255,.7);font-size:9.3px;line-height:13px;color:var(--white);text-align:justify}
.side-item:last-child{border-bottom:none}
.side-item .who{display:block;text-align:right;font-family:"Cabin",sans-serif;font-style:italic;font-size:12px;color:#7c4b22;margin-top:2px}
.side-item .date{display:block;text-align:right;font-size:10px;color:#6a4022;margin-right:10px}
.testimonials{left:675px;top:375px;width:225px;height:292px}
.news{left:675px;top:680px;width:218px;height:208px}
.practice{left:60px;top:628px;width:597px;height:280px;background:linear-gradient(180deg,#f8e7d6,#fdf6ee);border-radius:22px;box-shadow:0 2px 8px rgba(190,150,110,.3)}
.practice h2{position:absolute;left:37px;top:20px;font-family:"Cabin",sans-serif;font-weight:400;font-size:22px;color:var(--brown)}
.practice ul{position:absolute;list-style:none}
.practice li{height:22.2px;font-size:10.5px;color:#5a3a22;display:flex;align-items:center;gap:11px;white-space:nowrap}
.arrow-dot{width:13px;height:13px;border-radius:50%;background:var(--orange);position:relative;flex:none}
.arrow-dot::after{content:"";position:absolute;left:5px;top:3.5px;border-left:5px solid var(--white);border-top:3px solid transparent;border-bottom:3px solid transparent}
.col-left{left:48px;top:59px}
.col-right{left:323px;top:55px}
.cta{left:676px;top:895px;width:214px;height:63px;border-radius:4px;background:linear-gradient(180deg,#f2a65a,var(--orange-dark));box-shadow:0 2px 4px rgba(120,60,10,.4);font-family:"Cabin",sans-serif;color:var(--white);padding:12px 0 0 13px}
.cta .big{font-size:18px;line-height:20px}
.cta .small{font-size:12px;line-height:14px}
.cta-icon{position:absolute;right:14px;top:14px;width:32px;height:32px;background:var(--white);border-radius:7px;display:flex;align-items:center;justify-content:center}
.footer-wave{left:45px;top:925px}
.footer h3{font-family:"Cabin",sans-serif;font-weight:400;font-size:17px;color:var(--brown)}
.badge{background:#d8d2cc;border-radius:3px}
.pay-chip{top:1134px;width:28px;height:18px;background:var(--white);border:1px solid #cbbfb2;border-radius:2px;font-size:5px;color:var(--brown);display:flex;align-items:center;justify-content:center;font-weight:600;white-space:nowrap;overflow:hidden}
.social{top:1038px;width:34px;height:34px;border-radius:50%;background:var(--white);border:1px solid #d9cfc4;box-shadow:0 1px 3px rgba(0,0,0,.15);font-size:5.5px;color:var(--brown);display:flex;align-items:center;justify-content:center;font-weight:600;white-space:nowrap;overflow:hidden}
.footer-nav{top:1099px;left:527px;font-family:"Cabin",sans-serif;font-size:13px;color:var(--amber);font-weight:500;white-space:nowrap}
.footer-nav span{display:inline-block}
.copyright{top:1121px;right:83px;font-family:"Cabin",sans-serif;font-size:12.5px;color:var(--amber);font-weight:500;white-space:nowrap}
</style>
</head>
<body>
<div class="abs page"></div>

<svg class="abs header-swirl" width="480" height="180" viewBox="0 0 480 180" aria-hidden="true">
  <path d="M15 0 L420 0 C400 60 330 120 200 150 C120 168 50 170 20 160 C10 120 10 60 15 0Z" fill="#f8ebdd"/>
  <path d="M40 150 C150 150 330 110 400 10" fill="none" stroke="#f1dcc6" stroke-width="2"/>
</svg>

<div class="abs brand">
  <span class="brand-mark"></span>
  <span class="brand-name">Ashcombe Law</span>
</div>

<div class="abs phone-bar">
  <svg width="26" height="22" viewBox="0 0 26 22" aria-hidden="true">
    <path d="M2 8 C2 2 24 2 24 8 L20 10 L18 7 C15 6 11 6 8 7 L6 10Z" fill="#4a3020"/>
    <rect x="5" y="12" width="16" height="9" rx="2" fill="#4a3020"/>
  </svg>
  <span>CALL: 0 100 200 300</span>
</div>

<div class="abs hero-photo" role="img" aria-label="Photograph of a smiling family of four, children on their parents' shoulders"></div>

<div class="abs hero-box">
  <div class="line1">HELP WITH YOUR DIVORCE AND</div>
  <div class="line2">FAMILY LAW MATTERS</div>
</div>

<nav>
  <div class="abs nav-tab" style="left:80px;width:88px">Home</div>
  <div class="abs nav-tab" style="left:172px;width:125px">Meet Our Attorney</div>
  <div class="abs nav-tab" style="left:301px;width:88px">FAQ</div>
  <div class="abs nav-tab" style="left:393px;width:89px">Contact Us</div>
</nav>

<div class="abs content-band"></div>

<section class="abs about">
  <h1>About Ashcombe</h1>
  <h2>Help with Your Divorce and Family Law Matters</h2>
  <p>Divorce is a difficult and emotional situation, and the outcome could affect the individual and family for years to come. There are many tough decisions and matters to be resolved, including child custody, visitation, spousal support and issues regarding property division. These issues are often hotly contested and may be difficult to resolve amicably. A skilled divorce lawyer from our firm will provide the professional support needed to protect your interests. A Jacksonville family law attorney from The Law Offices of Martin R. Ellery, P.A. will provide experienced and dedicated legal counsel to assist in resolving all matters involved in the dissolution of a marriage, and we will stand firm in negotiating those matters that concern most.</p>
</section>

<aside class="abs side-card testimonials">
  <h3>Client Testimonials</h3>
  <div class="side-item">It is a long established fact that a reader will be distracted by the readable content of a page<span class="who">- Owen Petrak</span></div>
  <div class="side-item">It is a long established fact that a reader will be distracted by the readable content of a page<span class="who">- Owen Petrak</span></div>
  <div class="side-item">It is a long established fact that a reader will be distracted by the readable content of a page<span class="who">- Owen Petrak</span></div>
</aside>

<section class="abs practice">
  <h2>Area of Practice</h2>
  <ul class="col-left">
    <li><span class="arrow-dot"></span>Jacksonville Divorce Lawyer</li>
    <li><span class="arrow-dot"></span>Family Law Firm</li>
    <li><span class="arrow-dot"></span>Jacksonville Divorce Attorney</li>
    <li><span class="arrow-dot"></span>Meet Our Attorneys&nbsp;&nbsp;&nbsp; Frequently&nbsp;&nbsp; Asked</li>
    <li><span class="arrow-dot"></span>Questions&nbsp;&nbsp;&nbsp;&nbsp;&nbsp;&nbsp; Why Martin Ellery?</li>
    <li><span class="arrow-dot"></span>Contact Our Firm</li>
    <li><span class="arrow-dot"></span>Family Law Areas of Practice</li>
    <li><span class="arrow-dot"></span>Family Law</li>
  </ul>
  <ul class="col-right">
    <li><span class="arrow-dot"></span>Mothers' Rights</li>
    <li><span class="arrow-dot"></span>Palimony</li>
    <li><span class="arrow-dot"></span>Parental Alienation</li>
    <li><span class="arrow-dot"></span>Paternity</li>
    <li><span class="arrow-dot"></span>Prenuptial Agreements</li>
    <li><span class="arrow-dot"></span>Postnuptial Agreements</li>
    <li><span class="arrow-dot"></span>Property Division</li>
    <li><span class="arrow-dot"></span>Relocation</li>
  </ul>
</section>

<aside class="abs side-card news">
  <h3>Latest News</h3>
  <div class="side-item">It is a long established fact that a reader will be distracted by the readable content of a page<span class="date">Mar 10, 2012</span></div>
  <div class="side-item">It is a long established fact that a reader will be distracted by the readable content of a page<span class="date">Mar 10, 2012</span></div>
</aside>

<a class="abs cta">
  <div class="big">CALL TO ACTION</div>
  <div class="small">CLICK HERE TO CONTACT</div>
  <span class="cta-icon">
    <svg width="16" height="20" viewBox="0 0 16 20" aria-hidden="true"><path d="M3 1 L7 1 L8 6 L5 8 C6 11 8 13 10 14 L12 11 L16 13 L15 18 C8 19 1 11 1 3Z" fill="#e07a22"/></svg>
  </span>
</a>

<svg class="abs footer-wave" width="878" height="60" viewBox="0 0 878 60" aria-hidden="true">
  <path d="M0 20 C200 -5 420 30 600 38 C720 44 820 38 878 30 L878 60 L0 60Z" fill="#f4b27a"/>
  <path d="M0 30 C200 8 420 42 600 48 C720 52 820 46 878 40 L878 60 L0 60Z" fill="#fbeee0"/>
</svg>

<footer class="footer">
  <h3 class="abs" style="left:70px;top:997px">Our Certifications</h3>
  <div class="abs badge" style="left:70px;top:1043px;width:102px;height:70px"></div>
  <div class="abs badge" style="left:210px;top:1056px;width:146px;height:62px"></div>
  <div class="abs badge" style="left:384px;top:1045px;width:49px;height:77px;background:#6b625c"></div>

  <div class="abs pay-chip" style="left:68px">Tallipay</div>
  <div class="abs pay-chip" style="left:101px">Corvane</div>
  <div class="abs pay-chip" style="left:134px">Ombrix</div>
  <div class="abs pay-chip" style="left:167px">Fennacard</div>
  <div class="abs pay-chip" style="left:200px">Velquor</div>

  <h3 class="abs" style="left:695px;top:1004px">Connect With Us</h3>
  <div class="abs social" style="left:686px">Kestova</div>
  <div class="abs social" style="left:728px">Brimlet</div>
  <div class="abs social" style="left:770px">Quillor</div>
  <div class="abs social" style="left:812px">Zentrave</div>
  <div class="abs social" style="left:853px">Marbellio</div>

  <div class="abs footer-nav"><span>Home</span><span style="margin-left:28px">|</span><span style="margin-left:12px">Meet Our Attorney</span><span style="margin-left:20px">|</span><span style="margin-left:20px">FAQ</span><span style="margin-left:10px">|</span><span style="margin-left:22px">Contact Us</span></div>
  <div class="abs copyright">Copyright @ 2012&nbsp; www.ashcombelaw-example.com</div>
</footer>
</body>
</html>
```